Redesign of Form/Document Navigation Page

I need a redesign of our document and navigation bar on the left. We want the same navigation bar layout/setup but want the buttons and typography to be simple and matching all over. The form needs to be aesthetically pleasing and fit within the page.

1st attachment is our Direct Deposit and the second is the form continued.

```html
<!DOCTYPE html>
<html lang="en">
<head>
<meta charset="utf-8">
<title>Employee Direct Deposit Enrollment Form</title>
<link href="https://fonts.googleapis.com/css2?family=Open+Sans:wght@400;600;700;800&display=swap" rel="stylesheet">
<style>
  :root {
    --navy: #27235c;
    --gold: #f0b11a;
    --green: #1f9e0b;
    --panel: #f7f7f7;
    --line: #c9c9c9;
    --text: #4a4a4a;
    --muted: #8a8a8a;
    --footer: #3f3f3f;
    --white: #ffffff;
  }
  * { box-sizing: border-box; margin: 0; padding: 0; }
  html, body { width: 1070px; height: 1200px; overflow: hidden; background: var(--white); }
  body { font-family: "Open Sans", sans-serif; color: var(--text); }
  .page { position: relative; width: 1070px; height: 1200px; }
  .abs { position: absolute; }

  /* header */
  .brand { left: 67px; top: 24px; display: flex; align-items: center; gap: 8px; }
  .brand-mark { width: 32px; height: 32px; border-radius: 50%; background: var(--navy); }
  .brand-name { font-weight: 800; font-size: 19px; line-height: 1; color: var(--gold); text-transform: uppercase; width: 190px; }
  .btn-outline { left: 842px; top: 27px; width: 98px; height: 31px; border: 1px solid var(--line); border-radius: 2px; font-size: 12px; color: var(--navy); display: flex; align-items: center; justify-content: center; background: var(--white); }
  .user { left: 960px; top: 35px; font-size: 12px; font-weight: 700; color: var(--navy); display: flex; align-items: center; gap: 8px; }

  /* sidebar */
  .sidebar { left: 0; top: 78px; width: 282px; height: 1038px; background: var(--navy); }
  .nav-item { position: absolute; left: 67px; display: flex; align-items: center; gap: 14px; }
  .nav-icon { width: 35px; height: 35px; border: 2px solid var(--gold); border-radius: 50%; display: flex; align-items: center; justify-content: center; }
  .nav-label { font-size: 10.5px; font-weight: 700; color: var(--white); letter-spacing: 0.4px; text-transform: uppercase; }

  /* main */
  .main { left: 295px; top: 78px; width: 708px; height: 1038px; background: var(--panel); border-left: 1px solid #e4e4e4; border-right: 1px solid #e4e4e4; }
  .scroll-thumb { left: 991px; top: 101px; width: 5px; height: 38px; background: #c4c4c4; }
  .form-title { left: 319px; top: 96px; font-size: 20px; font-weight: 700; color: var(--navy); letter-spacing: 0.3px; text-transform: uppercase; }
  .copy { font-size: 11.5px; line-height: 21.5px; color: var(--text); }
  .intro { left: 319px; top: 125px; width: 660px; }
  .attach { left: 320px; top: 229px; width: 652px; height: 57px; background: var(--white); border: 1px solid #ececec; }
  .attach-text { left: 335px; top: 250px; font-size: 11.5px; color: var(--navy); }
  .btn-gold { background: var(--gold); color: var(--white); font-weight: 700; font-size: 11px; letter-spacing: 0.5px; display: flex; align-items: center; justify-content: center; gap: 7px; border-radius: 2px; text-transform: uppercase; }
  .refresh { left: 853px; top: 242px; width: 107px; height: 31px; }
  .section-head { font-size: 11.5px; font-weight: 700; color: var(--navy); text-transform: uppercase; letter-spacing: 0.2px; }
  .acct-head { left: 319px; top: 313px; }
  .acct-copy { left: 319px; top: 336px; }
  .strong { font-weight: 700; }
  .radio-row { display: flex; align-items: center; gap: 16px; font-size: 12px; color: var(--text); }
  .radio { display: flex; align-items: center; gap: 6px; }
  .radio::before { content: ""; width: 10px; height: 10px; border: 1px solid #9a9a9a; border-radius: 50%; background: var(--white); }
  .enroll { left: 317px; top: 416px; }
  .field { position: absolute; height: 32px; background: var(--white); border: 1px solid var(--line); font-size: 12px; color: var(--muted); padding: 0 10px; display: flex; align-items: center; }
  .acct-type { left: 770px; top: 504px; }
  .amount-label { left: 320px; top: 544px; font-size: 12px; color: var(--text); }
  .amount-value { left: 376px; top: 536px; width: 68px; height: 32px; background: var(--green); color: var(--white); font-size: 12px; font-weight: 700; padding-left: 12px; display: flex; align-items: center; }
  .percent { left: 453px; top: 545px; font-size: 11px; color: var(--text); }
  .important { left: 319px; top: 590px; font-size: 12px; font-weight: 700; color: var(--text); }
  .terms { left: 319px; top: 614px; width: 660px; line-height: 18px; }
  .emp-name { left: 319px; top: 716px; font-size: 11.5px; font-weight: 700; color: var(--text); }
  .emp-sig { left: 319px; top: 731px; font-size: 12px; color: var(--text); }
  .accept { left: 323px; top: 872px; width: 152px; height: 32px; font-size: 11.5px; }
  .payroll-head { left: 323px; top: 937px; width: 657px; text-align: center; font-size: 11.5px; font-weight: 700; color: var(--text); letter-spacing: 0.3px; text-transform: uppercase; }
  .payroll-box { left: 323px; top: 960px; width: 657px; height: 113px; border: 1px solid #b8b8b8; }
  .comments { align-items: flex-start; padding-top: 8px; }

  /* footer */
  .footer { left: 0; top: 1116px; width: 1070px; height: 84px; background: var(--footer); display: flex; align-items: center; justify-content: center; font-size: 12px; color: #b0b0b0; }
</style>
</head>
<body>
<div class="page">

  <header>
    <div class="abs brand">
      <span class="brand-mark"></span>
      <span class="brand-name">Sentinel Patrol Services</span>
    </div>
    <div class="abs btn-outline">Back to Profile</div>
    <div class="abs user">
      <svg width="11" height="11" viewBox="0 0 12 12" fill="none" stroke="#27235c" stroke-width="1.8" stroke-linecap="round"><path d="M3.5 3A4 4 0 1 0 8.5 3"/><path d="M6 1v5"/></svg>
      SPS
    </div>
  </header>

  <nav class="abs sidebar">
    <div class="nav-item" style="top:23px">
      <span class="nav-icon"><svg width="15" height="12" viewBox="0 0 15 12" fill="none" stroke="#fff" stroke-width="1.6"><rect x="1" y="1" width="13" height="10" rx="1.5"/><path d="M1 4.5h13"/><path d="M3 8h3"/></svg></span>
      <span class="nav-label">Direct Deposit</span>
    </div>
    <div class="nav-item" style="top:79px">
      <span class="nav-icon"><svg width="15" height="12" viewBox="0 0 15 12" fill="none" stroke="#fff" stroke-width="1.8"><path d="M2 4h11M10 1l3 3-3 3"/><path d="M13 8H2M5 5l-3 3 3 3"/></svg></span>
      <span class="nav-label">Change W-4</span>
    </div>
    <div class="nav-item" style="top:135px">
      <span class="nav-icon"><svg width="14" height="13" viewBox="0 0 14 13" fill="#fff"><rect x="0" y="0" width="3" height="3"/><rect x="5" y="0.5" width="9" height="2"/><rect x="0" y="5" width="3" height="3"/><rect x="5" y="5.5" width="9" height="2"/><rect x="0" y="10" width="3" height="3"/><rect x="5" y="10.5" width="9" height="2"/></svg></span>
      <span class="nav-label">Labour Code</span>
    </div>
    <div class="nav-item" style="top:191px">
      <span class="nav-icon"><svg width="6" height="13" viewBox="0 0 6 13" fill="#fff"><circle cx="3.5" cy="1.8" r="1.8"/><path d="M0 5h4.5v6H6v2H0v-2h1.5V7H0z"/></svg></span>
      <span class="nav-label">Personal Information</span>
    </div>
    <div class="nav-item" style="top:247px">
      <span class="nav-icon"><svg width="10" height="16" viewBox="0 0 10 16" fill="none" stroke="#fff" stroke-width="1.8"><path d="M5 0v16"/><path d="M9 4C8 2.5 6.5 2.5 5 2.5S1 3 1 5s2 2.5 4 3 4 1 4 3-1.5 2.5-4 2.5S1.5 13 1 11.5"/></svg></span>
      <span class="nav-label">Appraisal &amp; Review</span>
    </div>
    <div class="nav-item" style="top:303px">
      <span class="nav-icon"><svg width="12" height="15" viewBox="0 0 12 15"><path d="M0 0h8l4 4v11H0z" fill="#fff"/><path d="M3 7h6M3 9.5h6M3 12h6" stroke="#27235c" stroke-width="1"/></svg></span>
      <span class="nav-label">Write Up - Slip</span>
    </div>
    <div class="nav-item" style="top:359px">
      <span class="nav-icon"><svg width="16" height="13" viewBox="0 0 16 13" fill="#fff"><rect x="0" y="0" width="1.4" height="13"/><rect x="0" y="11.6" width="16" height="1.4"/><rect x="3" y="5" width="2" height="6"/><rect x="6.5" y="3" width="2" height="8"/><rect x="10" y="6" width="2" height="5"/><rect x="13" y="2" width="2" height="9"/></svg></span>
      <span class="nav-label">Employee Performance</span>
    </div>
  </nav>

  <main>
    <div class="abs main"></div>
    <div class="abs scroll-thumb"></div>

    <h1 class="abs form-title">Employee Direct Deposit Enrollment Form</h1>
    <p class="abs copy intro">Lorem ipsum dolor sit amet, consect- etuer adipiscing elit, sed diam nonummy nibh euismod tincidunt.<br>Aliquam molestie, mi et imperdiet euismod, dui purus auctor tellus, et interdum lacus lectus et ante. Sed accumsan sollicitudin sapien, sit amet adipiscing turpis gravida ac. In congue, neque ac lobortis volutpat, libero mauris varius mi, vitae suscipit ipsum ligula vitae risus. Duis aliquam nibh a dui iaculis viverra id a velit.</p>

    <div class="abs attach"></div>
    <div class="abs attach-text">Attach a Voided Check or Bank Deposit Form for the Account</div>
    <div class="abs btn-gold refresh">
      <svg width="11" height="11" viewBox="0 0 12 12" fill="none" stroke="#fff" stroke-width="1.8"><path d="M10.5 5A4.5 4.5 0 0 0 2 3.5M1.5 7A4.5 4.5 0 0 0 10 8.5"/><path d="M1.5 1v3h3M10.5 11V8h-3"/></svg>
      Refresh
    </div>

    <h2 class="abs section-head acct-head">Account Information</h2>
    <p class="abs copy acct-copy">Lorem ipsum dolor sit amet, consect- etuer adipiscing elit, sed diam nonummy nibh euismod tincidunt.<br><span class="strong">Make sure to indicate what kind of account, along with enrolling or declining.</span><br><span class="strong">**NOTIFY PAYROLL IMMEDIATELY IF YOU CLOSE OR CHANGE BANK ACCOUNT**</span></p>

    <div class="abs radio-row enroll">
      <span class="radio">New Enrollment</span>
      <span class="radio">Change Enrollment</span>
      <span class="radio">Cancel Enrollment</span>
    </div>

    <div class="field" style="left:320px;top:458px;width:216px">Bank Name</div>
    <div class="field" style="left:543px;top:458px;width:217px">City</div>
    <div class="field" style="left:766px;top:458px;width:216px;padding-left:18px">State</div>
    <div class="field" style="left:320px;top:496px;width:216px">Routing Transit #</div>
    <div class="field" style="left:543px;top:496px;width:217px">Account No.</div>
    <div class="abs radio-row acct-type">
      <span class="radio">Checking</span>
      <span class="radio">Saving</span>
    </div>

    <div class="abs amount-label">Amount</div>
    <div class="abs amount-value">100</div>
    <div class="abs percent">%</div>

    <div class="abs important">IMPORTANT! Please read and sign before completing and submitting.</div>
    <p class="abs copy terms">Lorem ipsum dolor sit amet, consect- etuer adipiscing elit, sed diam nonummy nibh euismod tincidunt. In congue, neque ac lobortis volutpat, libero mauris varius mi, vitae suscipit ipsum ligula vitae risus. Duis aliquam nibh a du iaculis viverra id a velit. Vivamus egestas risus in magna varius commodo.</p>

    <div class="abs emp-name">EMPLOYEE NAME:</div>
    <div class="abs emp-sig">Emplyoee Signature</div>
    <div class="field" style="left:323px;top:782px;width:216px"></div>
    <div class="field" style="left:556px;top:782px;width:216px;padding-left:7px">Sign Date</div>
    <div class="field" style="left:323px;top:822px;width:216px"></div>
    <div class="abs btn-gold accept">Accept Document</div>

    <div class="abs payroll-head">Only Payroll Manager Signs Below</div>
    <div class="abs payroll-box"></div>
    <div class="field" style="left:338px;top:982px;width:216px;padding-left:7px">Company Name</div>
    <div class="field" style="left:338px;top:1021px;width:216px;padding-left:7px">Emplyoee File Number</div>
    <div class="field comments" style="left:566px;top:982px;width:392px;height:71px;padding-left:7px">Comments:</div>
  </main>

  <footer class="abs footer">Copyright © 2016. Company Name. All Right Reserved</footer>
</div>
</body>
</html>
```